Audio and Video download site

I am looking for a good and beautiful website where users can be a able to download and upload musicial files and video file. Basically, there will be two categories. The first category for the music files( mp3, mva and other popular music files) while the second category will be for video files (mp4, wmv, divx and other files) users would be able to like and dislike a song/video. Users do not necessarily have to sign up for them to make you or download and upload files from the website. The website should be youthful.

```html
<!DOCTYPE html>
<html lang="en">
<head>
<meta charset="utf-8">
<title>Tunora — Music &amp; Video</title>
<link rel="stylesheet" href="https://fonts.googleapis.com/css2?family=Open+Sans:wght@400;600;700&family=Lato:wght@400;700;900&display=swap">
<style>
:root{
  --blue:#1b8fd6;
  --blue-dark:#1378b8;
  --orange:#f5842b;
  --ink:#333333;
  --muted:#8a8a8a;
  --line:#e2e2e2;
  --footer:#2c2c2c;
  --footer-text:#bdbdbd;
  --white:#ffffff;
  --rainbow:linear-gradient(90deg,#f0525f,#f7a541,#f4e04d,#7bd05a,#33b7e6,#7a6ee0,#e15fc4);
}
*{box-sizing:border-box;margin:0;padding:0}
html,body{width:1200px;height:2643px;overflow:hidden}
body{position:relative;background:var(--white);font-family:"Open Sans",Arial,sans-serif;color:var(--ink)}
a{color:inherit;text-decoration:none}
ul{list-style:none}

.rainbow-strip{position:absolute;left:0;top:0;width:1200px;height:4px;background:var(--rainbow)}

/* header */
.site-header{position:absolute;left:0;top:4px;width:1200px;height:105px}
.brand{position:absolute;left:99px;top:32px;font-family:"Lato",sans-serif;font-weight:900;font-size:38px;letter-spacing:2px;color:var(--blue)}
.upload-btn{position:absolute;left:862px;top:14px;width:100px;height:37px;background:var(--orange);color:var(--white);border-radius:3px;font-size:12px;font-weight:700;display:flex;align-items:center;justify-content:center;gap:6px}
.login-link{position:absolute;left:978px;top:26px;font-size:12px;color:var(--muted);display:flex;align-items:center;gap:8px}
.main-nav{position:absolute;right:99px;top:72px;display:flex;gap:24px;font-size:12.5px;font-weight:600;color:#444}
.main-nav a{display:flex;align-items:center;gap:7px;text-transform:uppercase}
.main-nav a.is-active{color:var(--blue)}
.main-nav svg{fill:currentColor}

/* hero */
.hero{position:absolute;left:0;top:109px;width:1200px;height:439px;background:linear-gradient(180deg,#2d6fc4 0%,#4a92d8 45%,#a9c8e2 72%,#e4ecf2 82%,#3e6b3e 100%);overflow:hidden}
.hero-title{position:absolute;left:0;width:100%;top:128px;text-align:center;color:var(--white);font-family:"Lato",sans-serif;font-size:27px;font-weight:700;letter-spacing:.5px}
.hero-sub{position:absolute;left:0;width:100%;top:170px;text-align:center;color:var(--white);font-size:25px;font-weight:700;font-style:italic}
.hero-search{position:absolute;left:317px;top:208px;width:566px;height:99px;background:rgba(20,40,70,.55);border:2px solid rgba(255,255,255,.5);border-radius:3px}
.hero-search-field{position:absolute;left:16px;top:35px;width:530px;height:44px;background:var(--white);display:flex;align-items:center;justify-content:space-between;padding:0 20px;font-size:12.5px;color:#555}
.hero-dots{position:absolute;top:382px;left:0;width:100%;display:flex;justify-content:center;gap:7px}
.hero-dots span{width:17px;height:17px;border-radius:50%;border:2px solid var(--white)}
.hero-dots span.is-current{background:var(--orange)}

/* section headings */
.section-head{position:absolute;left:99px;width:625px;height:38px;border-bottom:1px solid var(--line)}
.section-head h2{display:inline-block;height:38px;line-height:38px;padding:0 44px 0 25px;background:var(--blue);color:var(--white);font-family:"Lato",sans-serif;font-size:17px;font-weight:700;clip-path:polygon(0 0,88% 0,100% 100%,0 100%)}
.pager{position:absolute;right:0;top:4px;display:flex;gap:6px}
.pager span{width:26px;height:26px;border:1px solid #b8b8b8;border-radius:50%;display:flex;align-items:center;justify-content:center}

/* media grid */
.media-grid{position:absolute;left:99px;width:625px;display:grid;grid-template-columns:repeat(3,194px);column-gap:21px;row-gap:30px}
.tile{position:relative;height:176px}
.thumb{position:relative;width:194px;height:120px;border:3px solid #eeeeee;box-shadow:0 0 0 1px #dcdcdc}
.tile h3{margin-top:20px;font-size:13px;font-weight:700;color:#222}
.stats{margin-top:6px;display:flex;align-items:center;gap:5px;font-size:11px;color:var(--muted)}
.stats svg{fill:#9a9a9a}
.stats .sep{color:#bbb}
.thumb-format{position:absolute;left:10px;top:8px;font-size:11px;font-weight:700;color:var(--white)}
.thumb-play{position:absolute;left:0;right:0;top:52px;text-align:center;font-size:12px;font-weight:600;color:var(--white);letter-spacing:.3px}
.thumb-shade{position:absolute;inset:0;background:rgba(0,0,0,.35)}

.divider{position:absolute;left:99px;height:1px;background:var(--line)}

/* register */
.register{position:absolute;left:775px;top:596px;width:326px;height:410px;background:var(--blue);border:6px solid #f3f3f3;outline:1px solid #dcdcdc;color:var(--white);padding:0 20px}
.register h2{margin-top:18px;text-align:center;font-family:"Lato",sans-serif;font-size:21px;font-weight:700}
.field{margin-top:14px;height:38px;background:var(--white);color:#666;font-size:12px;display:flex;align-items:center;padding-left:17px}
.field:first-of-type{margin-top:28px}
.show-pass{text-align:right;font-size:11.5px;margin-top:8px}
.agree{margin-top:22px;display:flex;align-items:center;gap:14px;font-size:11.5px}
.agree span.box{width:22px;height:22px;border:2px solid var(--white)}
.register-actions{margin-top:28px;display:flex;align-items:center;gap:16px;font-size:12px;font-weight:700}
.register-btn{width:122px;height:37px;background:var(--orange);border-radius:3px;display:flex;align-items:center;justify-content:center;font-size:13px}
.register-actions a.login{text-decoration:underline}
.join{margin-top:14px;display:flex;align-items:center;gap:18px;font-size:12px;font-weight:600}
.join a{text-decoration:underline}
.join .square{width:16px;height:16px;background:var(--white)}

/* categories */
.categories{position:absolute;left:775px;top:1057px;width:326px;height:488px;border:1px solid var(--line);border-top:none}
.categories h2{height:39px;line-height:39px;display:inline-block;padding:0 36px 0 22px;background:var(--blue);color:var(--white);font-family:"Lato",sans-serif;font-size:17px;font-weight:700;clip-path:polygon(0 0,90% 0,100% 100%,0 100%)}
.categories .head-line{position:absolute;left:0;right:0;top:38px;height:1px;background:var(--line)}
.cat-list li{height:49px;line-height:49px;padding-left:22px;border-bottom:1px solid var(--line);font-size:12px;color:#555;text-transform:uppercase}
.view-more{position:absolute;right:18px;bottom:20px;font-size:11.5px;font-weight:700;color:var(--orange)}

/* comment */
.comment-title{position:absolute;left:99px;top:2066px;font-family:"Lato",sans-serif;font-size:17px;font-weight:700;color:#222}
.comment-box{position:absolute;left:99px;top:2111px;width:1002px;height:158px;border:1px solid #d4d4d4;border-radius:3px}
.avatar{position:absolute;left:42px;top:14px;width:79px;height:80px;background:linear-gradient(180deg,#dbe9fa,#b8d2f1)}
.comment-input{position:absolute;left:148px;top:14px;width:806px;height:80px;border:1px solid #d4d4d4;padding:14px 18px;font-size:11.5px;color:#999}
.plugin{position:absolute;left:148px;top:106px;display:flex;align-items:center;gap:10px;font-size:14px;color:#555}
.plugin span.square{width:14px;height:14px;background:#3b5998}
.plugin a{text-decoration:underline}
.comment-btn{position:absolute;left:856px;top:105px;width:94px;height:34px;background:var(--orange);border-radius:3px;color:var(--white);font-size:12px;font-weight:700;display:flex;align-items:center;justify-content:center}

/* footer */
.site-footer{position:absolute;left:0;top:2326px;width:1200px;height:317px;background:var(--footer);color:var(--footer-text)}
.site-footer::before{content:"";position:absolute;left:0;top:0;width:100%;height:4px;background:var(--rainbow)}
.footer-brand{position:absolute;left:99px;top:46px;font-family:"Lato",sans-serif;font-weight:900;font-size:38px;letter-spacing:2px;color:var(--blue)}
.footer-about{position:absolute;left:99px;top:106px;width:240px;font-size:12px;line-height:19px}
.footer-col{position:absolute;top:32px;font-size:11.5px}
.footer-col h4{font-family:"Lato",sans-serif;font-size:15px;font-weight:700;color:var(--white);margin-bottom:16px}
.footer-col li{line-height:26.5px}
.footer-col.downloads li{line-height:19px;margin-bottom:21px}
.footer-col.downloads .date{display:flex;align-items:center;gap:6px}
.footer-col.downloads .date svg{fill:var(--footer-text)}
.footer-col.with-rule{border-left:1px solid #3c3c3c;padding-left:0}
.footer-rule{position:absolute;left:99px;top:256px;width:1002px;height:1px;background:#3c3c3c}
.copyright{position:absolute;left:99px;top:276px;font-size:11.5px}
.social{position:absolute;right:99px;top:270px;display:flex;gap:12px}
.social span{width:24px;height:24px;border-radius:4px;background:#cfcfcf}
</style>
</head>
<body>

<svg width="0" height="0" style="position:absolute">
  <defs>
    <symbol id="i-head" viewBox="0 0 12 12"><path d="M1 8a5 5 0 0 1 10 0v3H9V8h1a4 4 0 0 0-8 0h1v3H1z"/></symbol>
    <symbol id="i-chat" viewBox="0 0 12 12"><path d="M1 2h10v6H5l-3 3V8H1z"/></symbol>
    <symbol id="i-up" viewBox="0 0 12 12"><path d="M1 5h2v6H1zM4 5l3-4 1 1-1 3h4v3l-2 3H4z"/></symbol>
    <symbol id="i-down" viewBox="0 0 12 12"><path d="M1 1h2v6H1zM4 7l3 4 1-1-1-3h4V4L9 1H4z"/></symbol>
    <symbol id="i-cal" viewBox="0 0 12 12"><path d="M1 2h10v9H1zM2 4v6h8V4zM3 0h2v3H3zM7 0h2v3H7z"/></symbol>
  </defs>
</svg>

<div class="rainbow-strip"></div>

<header class="site-header">
  <div class="brand">TUNORA</div>
  <a class="upload-btn" href="#"><svg width="11" height="11" viewBox="0 0 12 12" fill="#fff"><path d="M6 0l5 5H8v4H4V5H1zM0 10h12v2H0z"/></svg>UPLOAD</a>
  <a class="login-link" href="#"><svg width="11" height="11" viewBox="0 0 12 12" fill="#9a9a9a"><circle cx="6" cy="3.5" r="3"/><path d="M0 12a6 5 0 0 1 12 0z"/></svg>LOGIN / REGISTER</a>
  <nav class="main-nav">
    <a class="is-active" href="#"><svg width="12" height="11" viewBox="0 0 12 11"><path d="M6 0l6 5h-2v6H7V7H5v4H2V5H0z"/></svg>Home</a>
    <a href="#"><svg width="11" height="11" viewBox="0 0 12 12"><circle cx="6" cy="3.5" r="3"/><path d="M0 12a6 5 0 0 1 12 0z"/></svg>About</a>
    <a href="#"><svg width="11" height="11" viewBox="0 0 12 12"><path d="M4 1l8-1v9a2 2 0 1 1-1-1.7V3L5 4v7a2 2 0 1 1-1-1.7z"/></svg>Musics</a>
    <a href="#"><svg width="13" height="10" viewBox="0 0 13 10"><path d="M0 1h9v8H0zM9 4l4-3v8L9 6z"/></svg>Videos</a>
    <a href="#"><svg width="13" height="10" viewBox="0 0 13 10"><path d="M0 0h13v10H0zM2 2v6h4V2zm6 0v1h3V2zm0 2v1h3V4zm0 2v1h3V6z"/></svg>News &amp; Features</a>
    <a href="#"><svg width="13" height="10" viewBox="0 0 13 10"><path d="M0 0h13v1L6.5 5 0 1zM0 2.5l6.5 4 6.5-4V10H0z"/></svg>Contact Us</a>
  </nav>
</header>

<section class="hero" role="img" aria-label="Hot air balloons floating over a snowy mountain range under a blue sky">
  <h1 class="hero-title">WELCOME TO TUNORA!</h1>
  <p class="hero-sub">Get Your Video and Music Files in Our Chart to be Featured</p>
  <div class="hero-search">
    <div class="hero-search-field">SEARCH FOR MUSIC, VIDEOS
      <svg width="16" height="16" viewBox="0 0 16 16" fill="none" stroke="#777" stroke-width="2"><circle cx="6.5" cy="6.5" r="5"/><path d="M10 10l5 5"/></svg>
    </div>
  </div>
  <div class="hero-dots"><span class="is-current"></span><span></span><span></span><span></span></div>
</section>

<!-- newest musics -->
<div class="section-head" style="top:596px">
  <h2>NEWEST MUSICS</h2>
  <div class="pager">
    <span><svg width="7" height="10" viewBox="0 0 7 10" fill="none" stroke="#888" stroke-width="1.5"><path d="M6 1L2 5l4 4"/></svg></span>
    <span><svg width="7" height="10" viewBox="0 0 7 10" fill="none" stroke="#888" stroke-width="1.5"><path d="M1 1l4 4-4 4"/></svg></span>
  </div>
</div>

<div class="media-grid" style="top:664px">
  <article class="tile">
    <div class="thumb" role="img" aria-label="Bride sitting by the sea, music cover" style="background:linear-gradient(135deg,#7fa7a8,#c8d3cf)">
      <div class="thumb-shade"></div>
      <span class="thumb-format">MP3, MVA, MORE</span>
      <span class="thumb-play">PLAY OR DOWNLOAD</span>
    </div>
    <h3>SED UT PERSATIS UNDE</h3>
    <div class="stats"><svg width="10" height="10"><use href="#i-head"/></svg>2 <span class="sep">|</span><svg width="10" height="10"><use href="#i-chat"/></svg>0 <span class="sep">|</span><svg width="10" height="10"><use href="#i-up"/></svg>0 <span class="sep">|</span><svg width="10" height="10"><use href="#i-down"/></svg>0</div>
  </article>
  <article class="tile">
    <div class="thumb" role="img" aria-label="Band performing on a dark stage" style="background:linear-gradient(135deg,#1c1c1c,#6b5a4c)"></div>
    <h3>SED UT PERSATIS UNDE</h3>
    <div class="stats"><svg width="10" height="10"><use href="#i-head"/></svg>2 <span class="sep">|</span><svg width="10" height="10"><use href="#i-chat"/></svg>0 <span class="sep">|</span><svg width="10" height="10"><use href="#i-up"/></svg>0 <span class="sep">|</span><svg width="10" height="10"><use href="#i-down"/></svg>0</div>
  </article>
  <article class="tile">
    <div class="thumb" role="img" aria-label="Singer with a burst of purple paint" style="background:linear-gradient(135deg,#4b2a5e,#b98ab8)"></div>
    <h3>SED UT PERSATIS UNDE</h3>
    <div class="stats"><svg width="10" height="10"><use href="#i-head"/></svg>2 <span class="sep">|</span><svg width="10" height="10"><use href="#i-chat"/></svg>0 <span class="sep">|</span><svg width="10" height="10"><use href="#i-up"/></svg>0 <span class="sep">|</span><svg width="10" height="10"><use href="#i-down"/></svg>0</div>
  </article>
  <article class="tile">
    <div class="thumb" role="img" aria-label="Guitar strings in black and white" style="background:linear-gradient(135deg,#111,#8a8a8a)"></div>
    <h3>SED UT PERSATIS UNDE</h3>
    <div class="stats"><svg width="10" height="10"><use href="#i-head"/></svg>2 <span class="sep">|</span><svg width="10" height="10"><use href="#i-chat"/></svg>0 <span class="sep">|</span><svg width="10" height="10"><use href="#i-up"/></svg>0 <span class="sep">|</span><svg width="10" height="10"><use href="#i-down"/></svg>0</div>
  </article>
  <article class="tile">
    <div class="thumb" role="img" aria-label="Drum kit in a golden field" style="background:linear-gradient(180deg,#f1e6b4,#c99d3c)"></div>
    <h3>SED UT PERSATIS UNDE</h3>
    <div class="stats"><svg width="10" height="10"><use href="#i-head"/></svg>2 <span class="sep">|</span><svg width="10" height="10"><use href="#i-chat"/></svg>0 <span class="sep">|</span><svg width="10" height="10"><use href="#i-up"/></svg>0 <span class="sep">|</span><svg width="10" height="10"><use href="#i-down"/></svg>0</div>
  </article>
  <article class="tile">
    <div class="thumb" role="img" aria-label="Guitarist walking along railway tracks" style="background:linear-gradient(135deg,#5b5248,#a89a86)"></div>
    <h3>SED UT PERSATIS UNDE</h3>
    <div class="stats"><svg width="10" height="10"><use href="#i-head"/></svg>2 <span class="sep">|</span><svg width="10" height="10"><use href="#i-chat"/></svg>0 <span class="sep">|</span><svg width="10" height="10"><use href="#i-up"/></svg>0 <span class="sep">|</span><svg width="10" height="10"><use href="#i-down"/></svg>0</div>
  </article>
  <article class="tile">
    <div class="thumb" role="img" aria-label="Saxophone with sheet music" style="background:linear-gradient(135deg,#f2f2f2,#9b9b9b)"></div>
    <h3>SED UT PERSATIS UNDE</h3>
    <div class="stats"><svg width="10" height="10"><use href="#i-head"/></svg>2 <span class="sep">|</span><svg width="10" height="10"><use href="#i-chat"/></svg>0 <span class="sep">|</span><svg width="10" height="10"><use href="#i-up"/></svg>0 <span class="sep">|</span><svg width="10" height="10"><use href="#i-down"/></svg>0</div>
  </article>
  <article class="tile">
    <div class="thumb" role="img" aria-label="Electric guitar against a chalkboard wall" style="background:linear-gradient(135deg,#2a2a2a,#555)"></div>
    <h3>SED UT PERSATIS UNDE</h3>
    <div class="stats"><svg width="10" height="10"><use href="#i-head"/></svg>2 <span class="sep">|</span><svg width="10" height="10"><use href="#i-chat"/></svg>0 <span class="sep">|</span><svg width="10" height="10"><use href="#i-up"/></svg>0 <span class="sep">|</span><svg width="10" height="10"><use href="#i-down"/></svg>0</div>
  </article>
  <article class="tile">
    <div class="thumb" role="img" aria-label="Headphones with a glowing blue sound wave" style="background:linear-gradient(135deg,#02131f,#0a7ea6)"></div>
    <h3>SED UT PERSATIS UNDE</h3>
    <div class="stats"><svg width="10" height="10"><use href="#i-head"/></svg>2 <span class="sep">|</span><svg width="10" height="10"><use href="#i-chat"/></svg>0 <span class="sep">|</span><svg width="10" height="10"><use href="#i-up"/></svg>0 <span class="sep">|</span><svg width="10" height="10"><use href="#i-down"/></svg>0</div>
  </article>
</div>

<div class="divider" style="top:1292px;width:625px"></div>

<!-- newest videos -->
<div class="section-head" style="top:1334px">
  <h2>NEWEST VIDEOS</h2>
  <div class="pager">
    <span><svg width="7" height="10" viewBox="0 0 7 10" fill="none" stroke="#888" stroke-width="1.5"><path d="M6 1L2 5l4 4"/></svg></span>
    <span><svg width="7" height="10" viewBox="0 0 7 10" fill="none" stroke="#888" stroke-width="1.5"><path d="M1 1l4 4-4 4"/></svg></span>
  </div>
</div>

<div class="media-grid" style="top:1401px">
  <article class="tile">
    <div class="thumb" role="img" aria-label="Dancer with flowing hair and warm light" style="background:linear-gradient(135deg,#5a2a14,#f0d6b4)"></div>
    <h3>SED UT PERSATIS UNDE</h3>
    <div class="stats"><svg width="10" height="10"><use href="#i-head"/></svg>2 <span class="sep">|</span><svg width="10" height="10"><use href="#i-chat"/></svg>0 <span class="sep">|</span><svg width="10" height="10"><use href="#i-up"/></svg>0 <span class="sep">|</span><svg width="10" height="10"><use href="#i-down"/></svg>0</div>
  </article>
  <article class="tile">
    <div class="thumb" role="img" aria-label="Group jumping in a warm studio" style="background:linear-gradient(135deg,#c98a4a,#6b3a1e)"></div>
    <h3>SED UT PERSATIS UNDE</h3>
    <div class="stats"><svg width="10" height="10"><use href="#i-head"/></svg>2 <span class="sep">|</span><svg width="10" height="10"><use href="#i-chat"/></svg>0 <span class="sep">|</span><svg width="10" height="10"><use href="#i-up"/></svg>0 <span class="sep">|</span><svg width="10" height="10"><use href="#i-down"/></svg>0</div>
  </article>
  <article class="tile">
    <div class="thumb" role="img" aria-label="Skier jumping against a blue sky" style="background:linear-gradient(180deg,#3f7fd0,#e9f1f8)"></div>
    <h3>SED UT PERSATIS UNDE</h3>
    <div class="stats"><svg width="10" height="10"><use href="#i-head"/></svg>2 <span class="sep">|</span><svg width="10" height="10"><use href="#i-chat"/></svg>0 <span class="sep">|</span><svg width="10" height="10"><use href="#i-up"/></svg>0 <span class="sep">|</span><svg width="10" height="10"><use href="#i-down"/></svg>0</div>
  </article>
  <article class="tile">
    <div class="thumb" role="img" aria-label="Deer in a sunlit meadow" style="background:linear-gradient(180deg,#f4e3c1,#b5a34f)"></div>
    <h3>SED UT PERSATIS UNDE</h3>
    <div class="stats"><svg width="10" height="10"><use href="#i-head"/></svg>2 <span class="sep">|</span><svg width="10" height="10"><use href="#i-chat"/></svg>0 <span class="sep">|</span><svg width="10" height="10"><use href="#i-up"/></svg>0 <span class="sep">|</span><svg width="10" height="10"><use href="#i-down"/></svg>0</div>
  </article>
  <article class="tile">
    <div class="thumb" role="img" aria-label="Car driving on a snowy forest road" style="background:linear-gradient(180deg,#a9bdd3,#e8edf2)"></div>
    <h3>SED UT PERSATIS UNDE</h3>
    <div class="stats"><svg width="10" height="10"><use href="#i-head"/></svg>2 <span class="sep">|</span><svg width="10" height="10"><use href="#i-chat"/></svg>0 <span class="sep">|</span><svg width="10" height="10"><use href="#i-up"/></svg>0 <span class="sep">|</span><svg width="10" height="10"><use href="#i-down"/></svg>0</div>
  </article>
  <article class="tile">
    <div class="thumb" role="img" aria-label="Divers underwater" style="background:linear-gradient(180deg,#0f8fb0,#0b4f6a)"></div>
    <h3>SED UT PERSATIS UNDE</h3>
    <div class="stats"><svg width="10" height="10"><use href="#i-head"/></svg>2 <span class="sep">|</span><svg width="10" height="10"><use href="#i-chat"/></svg>0 <span class="sep">|</span><svg width="10" height="10"><use href="#i-up"/></svg>0 <span class="sep">|</span><svg width="10" height="10"><use href="#i-down"/></svg>0</div>
  </article>
  <article class="tile">
    <div class="thumb" role="img" aria-label="Swimmer splashing through water" style="background:linear-gradient(135deg,#27567c,#c4d8e6)"></div>
    <h3>SED UT PERSATIS UNDE</h3>
    <div class="stats"><svg width="10" height="10"><use href="#i-head"/></svg>2 <span class="sep">|</span><svg width="10" height="10"><use href="#i-chat"/></svg>0 <span class="sep">|</span><svg width="10" height="10"><use href="#i-up"/></svg>0 <span class="sep">|</span><svg width="10" height="10"><use href="#i-down"/></svg>0</div>
  </article>
  <article class="tile">
    <div class="thumb" role="img" aria-label="Runners racing on a track" style="background:linear-gradient(180deg,#3f7a3a,#b5543e)"></div>
    <h3>SED UT PERSATIS UNDE</h3>
    <div class="stats"><svg width="10" height="10"><use href="#i-head"/></svg>2 <span class="sep">|</span><svg width="10" height="10"><use href="#i-chat"/></svg>0 <span class="sep">|</span><svg width="10" height="10"><use href="#i-up"/></svg>0 <span class="sep">|</span><svg width="10" height="10"><use href="#i-down"/></svg>0</div>
  </article>
  <article class="tile">
    <div class="thumb" role="img" aria-label="Athlete stretching in a dark gym" style="background:linear-gradient(135deg,#1d2430,#5b6678)"></div>
    <h3>SED UT PERSATIS UNDE</h3>
    <div class="stats"><svg width="10" height="10"><use href="#i-head"/></svg>2 <span class="sep">|</span><svg width="10" height="10"><use href="#i-chat"/></svg>0 <span class="sep">|</span><svg width="10" height="10"><use href="#i-up"/></svg>0 <span class="sep">|</span><svg width="10" height="10"><use href="#i-down"/></svg>0</div>
  </article>
</div>

<!-- sidebar -->
<aside class="register">
  <h2>REGISTER FOR FREE</h2>
  <div class="field">NAME :</div>
  <div class="field">EMAIL :</div>
  <div class="field">PASSWORD :</div>
  <p class="show-pass">Show password</p>
  <label class="agree"><span class="box"></span>I agree to the terms of use &amp; Privacy Policy</label>
  <div class="register-actions"><a class="register-btn" href="#">REGISTER</a>OR <a class="login" href="#">LOG IN</a></div>
  <div class="join"><span class="square"></span><a href="#">Join with Friendzone</a></div>
</aside>

<aside class="categories">
  <h2>SEARCH BY CATEGORIES</h2>
  <div class="head-line"></div>
  <ul class="cat-list">
    <li>A to Z Songs</li>
    <li>A to Z Movies</li>
    <li>Remix</li>
    <li>Actor</li>
    <li>Actress</li>
    <li>Artist Collection</li>
    <li>Playlist</li>
    <li>Upgrade</li>
  </ul>
  <a class="view-more" href="#">VIEW MORE &gt;&gt;</a>
</aside>

<div class="divider" style="top:2032px;width:1002px"></div>

<!-- comment -->
<h2 class="comment-title">COMMENT</h2>
<div class="comment-box">
  <div class="avatar" role="img" aria-label="Default user avatar placeholder"></div>
  <div class="comment-input">ADD A COMMENT...</div>
  <div class="plugin"><span class="square"></span><a href="#">Friendzone social plugin</a></div>
  <a class="comment-btn" href="#">COMMENT</a>
</div>

<!-- footer -->
<footer class="site-footer">
  <div class="footer-brand">TUNORA</div>
  <p class="footer-about">At vero eos et accusamus et iusto odio dignissimos ducimus qui blanditiis praesentium voluptatum</p>

  <div class="footer-col" style="left:393px">
    <h4>ABOUT</h4>
    <ul><li>Home</li><li>About</li><li>Musics</li><li>Videos</li><li>News &amp; features</li><li>Contact Us</li></ul>
  </div>
  <div class="footer-col downloads" style="left:564px">
    <h4>DOWNLOADS</h4>
    <ul>
      <li>Finibus Bonorum et Malorum<span class="date"><svg width="10" height="10"><use href="#i-cal"/></svg>20/02/2016</span></li>
      <li>Finibus Bonorum et Malorum<span class="date"><svg width="10" height="10"><use href="#i-cal"/></svg>20/02/2016</span></li>
      <li>Finibus Bonorum et Malorum<span class="date"><svg width="10" height="10"><use href="#i-cal"/></svg>20/02/2016</span></li>
    </ul>
  </div>
  <div class="footer-col" style="left:812px">
    <h4>HELP</h4>
    <ul><li>Help Center</li><li>Video School</li><li>FAQ</li><li>Forums</li><li>Newsletter</li><li>Report on Issue</li></ul>
  </div>
  <div class="footer-col" style="left:974px">
    <h4>LEGAL</h4>
    <ul><li>Terms and Conditions</li><li>Privacy Policy</li><li>Sitemap</li><li>Cookies</li><li>Feedback</li></ul>
  </div>

  <div class="footer-rule"></div>
  <p class="copyright">Copyrights © 2016 Tunora, LLC. All rights reserved.</p>
  <div class="social"><span></span><span></span><span></span><span></span></div>
</footer>

</body>
</html>
```